Brovanek Data Yellow rose letterhead

I have a new logo for my company but in its current form it is too large to be used on letterhead or as a email signature. I need to have the designer use elements from the current logo and create something close to the original but more suited for smaller items.
Updates

I just uploaded a copy of our logo that does not have the weathered affect. Thanks

Reason: More time for revisions

Industry/Entity Type

It Company

Requirements
Must have
• The design must maintain the visual effect of the current logo. It needs to include the yellow rose and the name of the company.
Nice to have
• It would be nice to maintain the stamp theme and incorporate my name, address, phone, email. etc.

```html
<!DOCTYPE html>
<html lang="en">
<head>
<meta charset="utf-8">
<title>Brovanek Data – Stationery</title>
<link rel="stylesheet" href="https://fonts.googleapis.com/css2?family=Open+Sans:ital,wght@0,400;0,600;0,700;1,400;1,600;1,700&family=Alex+Brush&display=swap">
<style>
:root{
  --bg:#e9e9e9;
  --paper:#f7f7f7;
  --brown:#4f4440;
  --gold:#f0bf1a;
  --ink:#6b5f5a;
  --ink-dark:#4f4440;
}
*{margin:0;padding:0;box-sizing:border-box}
html,body{width:1200px;height:900px;overflow:hidden}
body{background:var(--bg);font-family:"Open Sans",Arial,sans-serif;color:var(--ink);position:relative}

.letterhead{position:absolute;left:82px;top:110px;width:508px;height:680px;background:var(--paper);overflow:hidden}
.envelope{position:absolute;background:var(--paper);overflow:hidden}
.envelope--back{left:638px;top:128px;width:540px;height:252px}
.envelope--front{left:638px;top:467px;width:537px;height:258px}

.brand-mark{position:absolute;display:flex;flex-direction:column;justify-content:center;align-items:flex-start;gap:6px;padding:6px;background:var(--brown)}
.brand-mark__square{width:16px;height:16px;background:var(--gold)}
.brand-mark__name{font-weight:700;font-size:14px;line-height:1.1;color:var(--gold)}

.letterhead .brand-mark{left:6px;top:8px;width:97px;height:85px}
.letterhead__rule{position:absolute;left:108px;top:8px;width:2px;height:115px;background:var(--gold)}
.sender{position:absolute;left:117px;top:14px;font-size:8px;line-height:11.5px;font-style:italic;color:var(--ink)}
.sender__name{font-size:10.5px;font-weight:700;color:var(--ink-dark);margin-bottom:1px}
.sender__email{margin-top:13px}
.tagline-band{position:absolute;left:0;top:98px;width:508px;height:25px;background:var(--brown);border-top:2px solid var(--gold)}
.tagline{position:absolute;left:114px;top:6px;font-size:7.6px;font-weight:600;color:#fff;white-space:nowrap}
.tagline strong{font-weight:700}

.recipient{position:absolute;left:114px;top:167px;font-size:7.6px;line-height:11px;font-style:italic}
.recipient__name{font-weight:600;color:var(--ink-dark)}
.letter-body{position:absolute;left:114px;top:229px;width:294px;font-size:7.3px;line-height:10.3px;text-align:justify}
.letter-body p{margin-bottom:8px}
.closing{position:absolute;left:114px;top:490px;font-size:7.4px}
.signature{position:absolute;left:112px;top:530px;font-family:"Alex Brush",cursive;font-size:19px;color:var(--ink-dark)}
.initials{position:absolute;left:114px;top:583px;font-size:7.4px}
.footer-swoosh{position:absolute;left:0;bottom:0;width:508px;height:150px}

.flap{position:absolute;left:0;top:0;width:540px;height:90px}
.envelope--back .brand-mark{left:222px;top:14px;width:80px;height:63px;gap:4px;padding:5px}
.envelope--back .brand-mark__name{font-size:11px}
.envelope--back .brand-mark__square{width:12px;height:12px}

.front-band{position:absolute;left:0;top:0;width:537px;height:15px;background:var(--brown)}
.front-stripe{position:absolute;left:0;top:18px;width:537px;height:7px;background:var(--gold)}
.envelope--front .brand-mark{left:15px;top:36px;width:85px;height:67px;gap:5px;padding:5px}
.envelope--front .brand-mark__name{font-size:12px}
.envelope--front .brand-mark__square{width:13px;height:13px}
.front-rule{position:absolute;left:108px;top:36px;width:2px;height:68px;background:var(--gold)}
.return-address{position:absolute;left:123px;top:47px;font-size:10px;line-height:13px;font-style:italic}
.return-address__name{font-weight:700;color:var(--ink-dark)}
</style>
</head>
<body>

<section class="letterhead">
  <div class="brand-mark"><span class="brand-mark__square"></span><span class="brand-mark__name">Brovanek Data</span></div>
  <div class="letterhead__rule"></div>
  <div class="sender">
    <div class="sender__name">Dr. Nadia Calloway</div>
    <div>410 Orchard Mesa Rd, Ste. 1200</div>
    <div>Millbrook, TX 76500</div>
    <div>(800) 555-0147</div>
    <div class="sender__email">nadia@brovanek-data.com</div>
  </div>
  <div class="tagline-band"><div class="tagline"><strong>CLEAR SIGNAL ANALYTICS:</strong>&nbsp; Turning Everyday Records Into Useful Customer Insight</div></div>

  <div class="recipient">
    <div class="recipient__name">Lena Marsh</div>
    <div>Brightfold Creative Services</div>
    <div>lena.brightfold@example.com</div>
    <div>817-555-0182</div>
  </div>

  <div class="letter-body">
    <p>Dear Nadia,<br>This text will be replaced by your own text. It has been a pleasure working with you. You are a rare and excellent communicator! I would love to talk to you about designing your business cards and web site.. Psed diam nonummy nibh euismod tincidunt ut laoreet dolore magna aliquam erat volutpat. Ut wisi enim ad minim veniam, quis nostrud exerci tation ullamcorper suscipit lobortis nisl ut aliquip ex ea commodo consequat. Duis autem vel eum iriure dolor in hendrerit in vulputate velit esse molestie consequat, vel illum dolore eu feugiat nulla facilisis at vero eros et accumsan et iusto odio dignissim qui blandit praesent luptatum zzril delenit augue duis dolore te feugait nulla facilisi.</p>
    <p>Ut wisi enim ad minim veniam, quis nostrud exerci tation ullamcorper suscipit lobortis nisl ut aliquip ex ea commodo consequat. Duis autem vel eum iriure dolor in hendrerit in vulputate velit esse molestie consequat, vel illum dolore eu feugiat nulla facilisis at vero eros et accumsan et iusto odio dignissim qui blandit praesent luptatum zzril delenit augue duis dolore te feugait nulla facilisi. Lorem ipsum dolor sit amet, consectetuer adipiscing elit, sed diam nonummy nibh euismod tincidunt ut laoreet dolore magna aliquam erat volutpat.</p>
    <p>Duis autem vel eum iriure dolor in hendrerit in vulputate velit esse molestie consequat, vel illum dolore eu feugiat nulla facilisis at vero eros et accumsan et iusto odio dignissim qui blandit praesent luptatum zzril delenit augue duis dolore te feugait nulla facilisi. Lorem ipsum dolor sit amet, consectetuer adipiscing elit, sed diam nonummy nibh euismod tincidunt ut laoreet dolore magna aliquam erat volutpat.</p>
  </div>
  <div class="closing">Sincerely,</div>
  <div class="signature">Lena Marsh</div>
  <div class="initials">lm/NC</div>

  <svg class="footer-swoosh" viewBox="0 0 508 150" role="img" aria-label="Speckled brown textured footer band">
    <path d="M0 128 C180 125 360 95 508 8 L508 150 L0 150 Z" fill="var(--brown)"/>
    <path d="M0 128 C180 125 360 95 508 8" fill="none" stroke="var(--gold)" stroke-width="2"/>
  </svg>
</section>

<section class="envelope envelope--back">
  <svg class="flap" viewBox="0 0 540 90" role="img" aria-label="Brushed brown envelope flap">
    <path d="M0 0 H540 L528 82 Q527 88 520 88 H20 Q13 88 12 82 Z" fill="var(--brown)"/>
    <line x1="8" y1="55" x2="536" y2="56" stroke="var(--gold)" stroke-width="2.5"/>
  </svg>
  <div class="brand-mark"><span class="brand-mark__square"></span><span class="brand-mark__name">Brovanek Data</span></div>
</section>

<section class="envelope envelope--front">
  <div class="front-band"></div>
  <div class="front-stripe"></div>
  <div class="brand-mark"><span class="brand-mark__square"></span><span class="brand-mark__name">Brovanek Data</span></div>
  <div class="front-rule"></div>
  <div class="return-address">
    <div class="return-address__name">Dr. Nadia Calloway</div>
    <div>410 Orchard Mesa Rd, Ste. 1200</div>
    <div>Millbrook, TX 76500</div>
  </div>
</section>

</body>
</html>
```